Sprout & Shine General Card Design

Please see http://sprout-and-shine.example.org for more information about our program. In brief, we are a 501(c)(3) nonprofit organization that focuses on improving educational outcomes for all students through parent education and empowerment, K-12 curriculum development, K-12 staff development, learner-oriented live events, community service projects, and more. We are now preparing to launch our Sprout & Shine Educational Series, which is devoted to teaching children and the adults in their lives about making healthy food choices and regaining control over what is in their food by growing it themselves in easy, affordable self-watering container gardens that can be placed in spaces not otherwise suitable for growing fruits and vegetables, such as paved lots and rooftops, are portable, and can be quickly built from recycled materials. In fact, we have local businesses already lining up to donate clean, safe 5-gallon buckets for this initiative (our container design uses 5-gallon buckets). We have already built out content on the site to support as many of the Trail Ranger merit badges as we could tie to the instructional goals of our Sprout & Shine Educational Series. We are in the processes of developing K-12 curricula tied to the Common Core and STEM (science, technology, engineering, & math), which we will be giving away for free under a Creative Commons license to help public schools in states that have recently adopted the Common Core but can't afford to replace all their textbooks and don't have the time to scramble to create curricula of their own. This card will be used by all of our Sprout & Shine staff and volunteers to share out information about the program and promote it to others. It will go out in mailings, sit on display tables at events, be left at kiosks, and be handed out in person. It needs to be color-matched to our Sprout & Shine site. The logo on the site we created for our Sprout & Shine Educational Series was done using an online service and the quality of the image is quite poor (see attached file). When we use it in print materials and then convert them to PDF, the logo becomes pixelated. It's awful. We are not entirely married to keeping the logo if you can come up with something better and we are given the final JPG or PNG file of the logo to upload to the site so they match. If you can just improve the quality of the existing logo, that's fine, too. Please note that the phrase "Sprout & Shine Educational Series" is a service mark of TMV4Families and should be followed by the letters "SM" in superscript at the end of the word "Series" in any logo you create.
Target Market(s)
parents of K-12 students, K-12 teachers, community service organizations, youth organizations, programs for the elderly, programs for the disabled
Industry/Entity Type
Community Service
Contact Information for Business Card
TMV4Families' Sprout & Shine Educational Series, http://sprout-and-shine.example.org, (555) 214-7390, Non-GMO/Organic Family & Community Gardening Workshops, K-12 Common Core/STEM Curricula Development, Community Service Projects, Online Gardening & Teaching Communities, Project-Based Learning Activities, Youth Leadership Projects, Fun Contests and Prizes, Corporate & Small Business Social Responsibility Programs, K-12 Staff Development, Education Research & Reporting

```html
<!DOCTYPE html>
<html lang="en">
<head>
<meta charset="utf-8">
<title>Sprout &amp; Shine Educational Series – Card</title>
<link rel="stylesheet" href="https://fonts.googleapis.com/css2?family=Didact+Gothic&family=Noto+Sans:wght@700&family=Arimo:wght@700&display=swap">
<style>
  :root {
    --page: #ffffff;
    --card-edge: #c9c9c9;
    --card-mid: #f4f4f4;
    --card-light: #ffffff;
    --heading-green: #4f8a2b;
    --deep-green: #0d4a12;
    --leaf-light: #9ed42a;
    --leaf-dark: #2f8f2a;
    --body-text: #3a3a3a;
    --bullet: #6aa84f;
  }
  * { box-sizing: border-box; margin: 0; padding: 0; }
  html, body {
    width: 941px; height: 1200px; overflow: hidden;
    background: var(--page);
  }
  .canvas { position: relative; width: 941px; height: 1200px; }

  .card {
    position: absolute; left: 83px; width: 764px; height: 454px;
    background: linear-gradient(90deg, var(--card-edge) 0%, var(--card-mid) 30%, var(--card-light) 55%, var(--card-mid) 82%, var(--card-edge) 100%);
    box-shadow: 0 10px 14px rgba(0,0,0,0.18);
    overflow: hidden;
  }
  .card--front { top: 70px; border-radius: 0 120px 0 130px; }
  .card--back  { top: 658px; border-radius: 130px 0 0 0; }

  .series-title {
    position: absolute; white-space: nowrap; z-index: 2;
    font-family: "Didact Gothic", "Century Gothic", sans-serif;
    color: var(--heading-green); font-weight: 400;
  }
  .series-title sup { font-size: 0.5em; vertical-align: 0.9em; margin-left: 2px; }
  .card--front .series-title { left: 0; right: 0; text-align: center; top: 44px; font-size: 37px; }
  .card--back .series-title { left: 70px; top: 56px; font-size: 40px; }

  .org-name {
    position: absolute; left: 0; right: 0; top: 150px; z-index: 2;
    display: flex; align-items: center; justify-content: center; gap: 16px;
    font-family: "Noto Sans", Verdana, sans-serif; font-weight: 700;
    font-size: 54px; color: var(--deep-green); letter-spacing: 0.5px;
  }
  .org-name__dot { width: 34px; height: 34px; border-radius: 50%; background: var(--deep-green); }

  .tagline {
    position: absolute; left: 0; right: 0; top: 276px; text-align: center; z-index: 2;
    font-family: "Noto Sans", Verdana, sans-serif; font-weight: 700;
    font-size: 20px; color: var(--deep-green);
  }
  .web {
    position: absolute; left: 250px; top: 325px; z-index: 2;
    font-family: "Noto Sans", Verdana, sans-serif; font-weight: 700;
    font-size: 17px; color: var(--deep-green);
  }
  .phone {
    position: absolute; right: 78px; top: 385px; z-index: 2;
    display: flex; align-items: center; gap: 8px;
    font-family: "Arimo", Arial, sans-serif; font-weight: 700;
    font-size: 22px; color: var(--deep-green);
  }
  .phone svg { width: 24px; height: 30px; }

  .leaves {
    position: absolute; z-index: 1;
    background: radial-gradient(ellipse at 60% 70%, var(--leaf-dark) 0%, var(--leaf-light) 55%, rgba(158,212,42,0) 75%);
  }
  .card--front .leaves { left: 0; top: 283px; width: 270px; height: 171px; border-radius: 0 90% 0 0; }
  .card--back .leaves { left: 479px; top: 272px; width: 285px; height: 182px; border-radius: 90% 0 0 0; }

  .services {
    position: absolute; left: 74px; top: 128px; list-style: none; z-index: 2;
    font-family: "Didact Gothic", "Century Gothic", sans-serif;
    font-size: 21px; letter-spacing: 0.3px; line-height: 26.6px; color: var(--body-text);
  }
  .services li { position: relative; padding-left: 18px; white-space: nowrap; }
  .services li::before {
    content: ""; position: absolute; left: 0; top: 11px;
    width: 6px; height: 6px; border-radius: 50%; background: var(--bullet);
  }
</style>
</head>
<body>
<main class="canvas">
  <section class="card card--front">
    <h1 class="series-title">Sprout &amp; Shine Educational Series<sup>SM</sup></h1>
    <div class="org-name"><span class="org-name__dot"></span><span>TMV4Families</span></div>
    <p class="tagline">Teaching Makes Victories for Families</p>
    <p class="web">http://sprout-and-shine.example.org</p>
    <p class="phone">
      <svg viewBox="0 0 24 30" aria-hidden="true"><path fill="currentColor" d="M6 2c1.5-1 3 0 3.5 1.5l1.5 4c.4 1.2 0 2.2-1 2.8l-1.6 1c.3 2.8 1.6 5.6 3.6 7.8l1.7-.8c1-.5 2.2-.2 2.9.8l2.4 3.4c.8 1.2.5 2.6-.7 3.3l-2 1.2C12 30 3 21 1.5 11.3 1 8 2.5 4.5 6 2z"/></svg>
      (555) 214-7390
    </p>
    <div class="leaves" role="img" aria-label="Green sprouting leaves illustration"></div>
  </section>

  <section class="card card--back">
    <h2 class="series-title">Sprout &amp; Shine Educational Series<sup>SM</sup></h2>
    <ul class="services">
      <li>Non-GMO/Organic Family &amp; Community Gardening Workshops</li>
      <li>K-12 Common Core/STEM Curricula Development</li>
      <li>Community Service Projects</li>
      <li>Online Gardening &amp; Teaching Communities</li>
      <li>Project-Based Learning Activities</li>
      <li>Youth Leadership Projects</li>
      <li>Fun Contests and Prizes</li>
      <li>Corporate &amp; Small Business Social Responsibility Programs</li>
      <li>K-12 Staff Development</li>
      <li>Education Research &amp; Reporting</li>
    </ul>
    <div class="leaves" role="img" aria-label="Green sprouting leaves illustration"></div>
  </section>
</main>
</body>
</html>
```